Fresh, modern, fun business card for pediatric dental practice

Need a business card for fresh, modern, fun pediatric dental practice

Clean look that matches our website's font and colors

We prefer the look of curved corners on business cards

Target Market(s)

parents (mothers) of young children, professionals, mid-high class

Industry/Entity Type

Dental

Contact Information for Business Card

Maplebrook Pediatric Dentistry
482 Quarry Lane
Suite 517
Cedarvale, PA 17590
717.555.0193
www.maplebrookkidsdental.example

Mei-Ran Tsai, DMD
Corinne Walbeck, DMD
(we are working on our email address, but we would like that on the card as well)

Font styles to use
Sans Serif

Requirements
Must have
• All info; we would also like to make cards for individual staff members
• colors from our website and color palatte, attatched
• use same font and design as website for branding
Nice to have
• clean, simple card that has a pop of color
• we would like to see a few designs with our tag line "where smiles get brighter"
• we are not sure if we want to have it on there or not
• we would like to see a few designs incorporating the ribbon graphic on our website where the word WELCOME is

```html
<!DOCTYPE html>
<html lang="en">
<head>
<meta charset="utf-8">
<title>Maplebrook Pediatric Dentistry – Business Card</title>
<link rel="stylesheet" href="https://fonts.googleapis.com/css2?family=Roboto:wght@400;500;700&display=swap">
<style>
  :root {
    --backdrop: #2b2b2d;
    --card: #262628;
    --sun-yellow: #f7b318;
    --text-white: #f4f4f4;
    --divider: #8a8a8c;
  }
  * { margin: 0; padding: 0; box-sizing: border-box; }
  html, body { width: 1200px; height: 900px; overflow: hidden; }
  body {
    background: var(--backdrop);
    font-family: "Roboto", Arial, sans-serif;
    position: relative;
  }
  .card {
    position: absolute;
    left: 290px;
    width: 620px;
    height: 354px;
    background: var(--card);
    border-radius: 18px;
    box-shadow: 0 10px 30px rgba(0,0,0,0.45);
  }
  .card-front { top: 70px; }
  .card-back { top: 474px; }

  /* Front */
  .brand {
    position: absolute;
    top: 62px;
    left: 0;
    width: 100%;
    text-align: center;
  }
  .brand-dot {
    display: block;
    width: 34px;
    height: 34px;
    margin: 0 auto 14px;
    border-radius: 50%;
    background: var(--sun-yellow);
  }
  .brand-name {
    color: var(--sun-yellow);
    font-weight: 700;
    font-size: 40px;
    line-height: 1.05;
    letter-spacing: 0.5px;
  }
  .front-url {
    position: absolute;
    bottom: 58px;
    left: 0;
    width: 100%;
    text-align: center;
    color: var(--text-white);
    font-size: 14px;
    font-weight: 500;
    letter-spacing: 4px;
  }

  /* Back */
  .doctors {
    position: absolute;
    right: 340px;
    top: 124px;
    text-align: right;
    color: var(--sun-yellow);
    font-weight: 700;
    font-size: 23px;
    line-height: 1.15;
    text-transform: uppercase;
  }
  .divider {
    position: absolute;
    left: 298px;
    top: 92px;
    width: 1px;
    height: 150px;
    background: linear-gradient(to bottom, transparent, var(--divider) 20%, var(--divider) 80%, transparent);
  }
  .contact {
    position: absolute;
    left: 318px;
    top: 102px;
    color: var(--text-white);
    font-size: 15.5px;
    font-weight: 500;
    line-height: 1.3;
  }
  .contact-address { margin-bottom: 12px; font-style: normal; }
  .contact-line {
    display: flex;
    align-items: center;
    gap: 8px;
  }
  .contact-line svg { width: 15px; height: 15px; flex: none; }
</style>
</head>
<body>

<section class="card card-front" aria-label="Card front">
  <div class="brand">
    <span class="brand-dot"></span>
    <div class="brand-name">Maplebrook<br>Pediatric Dentistry</div>
  </div>
  <div class="front-url">www.maplebrookkidsdental.example</div>
</section>

<section class="card card-back" aria-label="Card back">
  <div class="doctors">
    <p>Mei-Ran Tsai, DMD</p>
    <p>Corinne Walbeck, DMD</p>
  </div>
  <div class="divider"></div>
  <div class="contact">
    <address class="contact-address">
      Maplebrook Pediatric Dentistry<br>
      482 Quarry Lane<br>
      Suite 517<br>
      Cedarvale, PA 17590
    </address>
    <p class="contact-line">
      <svg viewBox="0 0 24 24" aria-hidden="true"><path fill="#f7b318" d="M6.6 10.8c1.4 2.8 3.8 5.1 6.6 6.6l2.2-2.2c.3-.3.7-.4 1-.2 1.1.4 2.300.6 3.6.6.6 0 1 .4 1 1V20c0 .6-.4 1-1 1C10.6 21 3 13.4 3 4c0-.6.4-1 1-1h3.5c.6 0 1 .4 1 1 0 1.3.2 2.5.6 3.6.1.3 0 .7-.2 1z"/></svg>
      717.555.0193
    </p>
    <p class="contact-line">
      <svg viewBox="0 0 24 24" aria-hidden="true"><circle cx="12" cy="12" r="10" fill="#f7b318"/><path d="M2 12h20M12 2c3 3 3 17 0 20M12 2c-3 3-3 17 0 20" stroke="#262628" stroke-width="1.6" fill="none"/></svg>
      maplebrookkidsdental.example
    </p>
  </div>
</section>

</body>
</html>
```